Verodex business card

Business card for sustainable investment company called "Verodex". Verodex is an exchange platform selling carbon credits between buyers and sellers. Carbon Credits are an environmental commodity for reducing global carbon emissions.

the card should obviously have our logo and the theme should be sustainability/environment mixed with a trading platform.

Contact Information for Business Card

Logo, Name, Title, Phone, Email

Colors
0054AA
0677BA
7BADD7
CADEEF
E8F1F8
0094D4
00A9DD
6FCCEA
C7EBF8
E9F6FB
00AB8E
00BBA5
67D7C9
C6EFE9
E9F9F6
59FF00
82FF00
B8FF75
E3FFCB
F4FFEA

```html
<!DOCTYPE html>
<html lang="en">
<head>
<meta charset="utf-8">
<title>Verodex business card</title>
<link rel="stylesheet" href="https://fonts.googleapis.com/css2?family=Poppins:wght@400;500;600;700&display=swap">
<style>
  :root{
    --bg:#2b2b2d;
    --navy:#1f3350;
    --navy-deep:#15243a;
    --ink:#1d2f4a;
    --blue:#0677BA;
    --bright:#0094D4;
    --cyan:#6FCCEA;
    --white:#ffffff;
    --rule:#b9bec6;
  }
  *{margin:0;padding:0;box-sizing:border-box}
  html,body{width:1200px;height:689px;overflow:hidden;background:var(--bg);font-family:"Poppins",sans-serif}
  .canvas{position:relative;width:1200px;height:689px}
  .card{position:absolute;top:190px;width:530px;height:310px;border-radius:18px;overflow:hidden}
  .card--back{left:45px;background:var(--navy)}
  .card--front{left:625px;background:var(--white)}
  .back-pattern{position:absolute;inset:0;
    background:radial-gradient(circle at 85% 10%,#3c5f92 0%,#243a5c 35%,#15243a 100%)}
  .back-brand{position:absolute;left:0;right:0;top:128px;text-align:center;
    color:var(--white);font-weight:600;font-size:44px;letter-spacing:3px}
  .front-brand{position:absolute;left:40px;top:128px;color:var(--ink);
    font-weight:600;font-size:36px;letter-spacing:2px;display:flex;align-items:center;gap:12px}
  .front-brand .mark{width:14px;height:14px;background:var(--bright)}
  .divider{position:absolute;left:268px;top:40px;width:1px;height:190px;
    background:linear-gradient(var(--white),var(--rule),var(--white))}
  .person{position:absolute;left:292px;top:58px}
  .person .name{color:var(--ink);font-weight:700;font-size:21px;letter-spacing:.5px}
  .person .title{color:var(--ink);font-weight:400;font-size:13px;margin-top:-2px}
  .contacts{list-style:none;margin-top:26px}
  .contacts li{display:flex;align-items:center;gap:9px;color:var(--ink);font-size:14px;line-height:22px}
  .contacts svg{width:13px;height:13px;flex:none}
  .footer-band{position:absolute;left:0;right:0;bottom:0;height:42px;background:var(--navy)}
  .footer-line{position:absolute;left:0;right:0;bottom:46px;height:5px;
    background:linear-gradient(90deg,var(--blue),var(--cyan) 55%,var(--blue))}
</style>
</head>
<body>
<main class="canvas">
  <section class="card card--back">
    <div class="back-pattern" role="img" aria-label="Embossed repeating brand pattern on dark navy"></div>
    <div class="back-brand">VERODEX</div>
  </section>

  <section class="card card--front">
    <div class="front-brand"><span class="mark"></span>VERODEX</div>
    <div class="divider"></div>
    <div class="person">
      <div class="name">MARCUS HALE</div>
      <div class="title">Managing Director</div>
      <ul class="contacts">
        <li><svg viewBox="0 0 24 24"><path fill="#1d2f4a" d="M6.6 10.8a15 15 0 006.6 6.6l2.2-2.2c.3-.3.7-.4 1-.2 1.1.4 2.3.6 3.6.6.6 0 1 .4 1 1V20c0 .6-.4 1-1 1A17 17 0 013 4c0-.6.4-1 1-1h3.5c.6 0 1 .4 1 1 0 1.3.2 2.5.6 3.6.1.3 0 .7-.2 1z"/></svg>044-987 654 321</li>
        <li><svg viewBox="0 0 24 24"><path fill="#1d2f4a" d="M2 5h20v14H2z"/><path fill="none" stroke="#fff" stroke-width="2" d="M2 5l10 8 10-8"/></svg>info@verodexmail.com</li>
        <li><svg viewBox="0 0 24 24" fill="none" stroke="#1d2f4a" stroke-width="2"><circle cx="12" cy="12" r="10"/><path d="M2 12h20M12 2c3 3 3 17 0 20M12 2c-3 3-3 17 0 20"/></svg>www.verodexhub.com</li>
      </ul>
    </div>
    <div class="footer-line"></div>
    <div class="footer-band"></div>
  </section>
</main>
</body>
</html>
```